we can communicate on this, but i want to follow the approach we took on Pellew|Marsh & Quinlan but i feel the card front needs the black background and the platinum and gold logo. The back? I am open. we can use the same info from PM&Q. Velmont Arc is an enhanced equity investment fund - basically a very exclusive boutique hedge fund that uses only stock options. very advanced things. hope you are interested

Contact Information for Business Card

Dr. Lewis T. Brennick, CFA
Scientifique de fusée financière
701.555.0143
LTBquant47@mailvantor.com

4718 Willow Creek Bend W.
West Fargo, ND 58078

No web site

Colors

Designer to choose colors to be used in the design.

Requirements
Nice to have
• I tend to prefer the most visible applications of the logo to include logo and name, the logo version with a black background and the gold and platinum components separated by the black. I see this working well for a single side (logo and name - this is card front to me).
• I am fairly open to other treatments on the reverse side with the data. To me, it makes sense to have a different color rendition of the logo on the reverse and it may be a muted black tone on tone or an oversized portion that would have spot UV. Or, the reverse may play with colors and layout
Should not have
• Other colors = no no
• Decorative font

```html
<!DOCTYPE html>
<html lang="en">
<head>
<meta charset="utf-8">
<title>Velmont Arc — Business Card</title>
<link rel="stylesheet" href="https://fonts.googleapis.com/css2?family=Open+Sans:wght@400;600;700&display=swap">
<style>
  :root {
    --backdrop: #d9d6d1;
    --card-light: #ffffff;
    --card-dark: #151515;
    --gold: #c9a12a;
    --ink: #111111;
    --ink-soft: #222222;
    --white: #ffffff;
    --rule: #1a1a1a;
  }
  * { margin: 0; padding: 0; box-sizing: border-box; }
  html, body {
    width: 1200px; height: 1000px; overflow: hidden;
    background: var(--backdrop);
    font-family: "Open Sans", Arial, sans-serif;
  }
  .canvas { position: relative; width: 1200px; height: 1000px; }

  .card {
    position: absolute;
    border-radius: 24px;
    box-shadow: 0 6px 16px rgba(0,0,0,0.22);
  }
  .card--info { left: 262px; top: 74px; width: 666px; height: 397px; background: var(--card-light); }
  .card--brand { left: 267px; top: 533px; width: 665px; height: 397px; background: var(--card-dark); }

  .brand-mark {
    position: absolute;
    border-radius: 50%;
    background: var(--gold);
  }
  .brand-name {
    position: absolute;
    text-align: center;
    font-weight: 700;
    line-height: 1;
  }
  .brand-name span { display: block; }

  .card--info .brand-mark { left: 106px; top: 98px; width: 106px; height: 106px; }
  .card--info .brand-name { left: 24px; width: 270px; top: 236px; color: var(--ink); font-size: 44px; letter-spacing: 1px; }
  .card--info .brand-name .brand-name__second { font-size: 24px; letter-spacing: 8px; margin-top: 10px; }

  .card--brand .brand-mark { left: 259px; top: 75px; width: 146px; height: 146px; }
  .card--brand .brand-name { left: 82px; width: 500px; top: 243px; color: var(--white); font-size: 58px; letter-spacing: 2px; }
  .card--brand .brand-name .brand-name__second { font-size: 30px; letter-spacing: 10px; margin-top: 12px; }

  .divider {
    position: absolute; left: 322px; top: 98px;
    width: 2px; height: 204px; background: var(--rule);
  }

  .contact { position: absolute; left: 345px; top: 116px; color: var(--ink-soft); font-size: 17px; line-height: 1.3; }
  .contact__name { color: var(--gold); font-weight: 700; font-size: 17px; text-transform: uppercase; white-space: nowrap; }
  .contact__title { margin-top: 2px; white-space: nowrap; }
  .contact__address { margin-top: 10px; line-height: 22px; }
  .contact__list { list-style: none; margin-top: 8px; }
  .contact__list li { display: flex; align-items: center; height: 24.5px; font-size: 17px; white-space: nowrap; }
  .contact__list svg { width: 15px; height: 15px; margin-right: 8px; flex: none; }
</style>
</head>
<body>
<main class="canvas">

  <section class="card card--info" aria-label="Card side with contact details">
    <div class="brand-mark" aria-hidden="true"></div>
    <div class="brand-name"><span>VELMONT</span><span class="brand-name__second">ARC</span></div>
    <div class="divider"></div>
    <div class="contact">
      <p class="contact__name">Dr. Lewis T. Brennick, CFA</p>
      <p class="contact__title">Scientifique de fusée financière</p>
      <p class="contact__address">4718 Willow Creek Bend W.<br>West Fargo, ND 58078</p>
      <ul class="contact__list">
        <li>
          <svg viewBox="0 0 16 16" aria-hidden="true"><path fill="#c9a12a" d="M2 5c0-2 3-3 6-3s6 1 6 3v1h-3V5H5v1H2zM4 7h8l2 6H2z"/><circle cx="8" cy="10" r="1.6" fill="#fff"/></svg>
          701.555.0143
        </li>
        <li>
          <svg viewBox="0 0 16 16" aria-hidden="true"><rect x="1" y="3" width="14" height="10" rx="1" fill="#c9a12a"/><path d="M1.5 3.5 8 9l6.5-5.5" stroke="#fff" stroke-width="1.3" fill="none"/></svg>
          LTBquant47@mailvantor.com
        </li>
      </ul>
    </div>
  </section>

  <section class="card card--brand" aria-label="Card side with brand name">
    <div class="brand-mark" aria-hidden="true"></div>
    <div class="brand-name"><span>VELMONT</span><span class="brand-name__second">ARC</span></div>
  </section>

</main>
</body>
</html>
```